Valdane Companies Business Card Design

We need a new business card for our Private Equity Real Estate Development firm, “Valdane” and our EB-5 regional center “Thornmere Regional Center” on one card. We prefer a design that is simple, elegant, and represents the luxury products we design and build as well as the financial security and stability our successful history has produced. We are an industry leader in our field and 3rd generation family business that has evolved into an institutional quality investment platform. Considered design size is standard business card dimensions (3.5 x 2 inches with an additional 1/8 inch space for design elements or backgrounds that extend beyond the finished size of your piece.

Target Market(s)

• High net worth individuals
• Highly skilled technical workers and physicians in the US seeking investment-based immigration opportunities
• Sophisticated private equity investors
• Intermediary partners include domestic attorneys and investment brokers, as well as international agent networks
• US real estate developers

Industry/Entity Type

Finance

Contact Information for Business Card

(Providing placeholder info for personal information, please design for longer character spaces, longer names and addresses etc..)
• Logo for Valdane
• Logo for Thornmere Regional Center
• Full name: Marcus Valdane
• Job title: CEO
• Email address: mvaldane@valdanecompanies.com
• Cell phone number: +1.555.314.2287
• Office number +1.555.628.4410
• Office address: Larkfield Court 5, 4817 Vista Orilla, Alder Vale, CA.
• Website: www.valdanecompanies.com

Font styles to use
Serif
Sans Serif

Colors
ec1f27
ffffff
000000

Requirements
Must have
• • Logo for Valdane
• • Logo for Thornmere Regional Center
• - Use rounded corners
• (See .ai file included for logos)
Nice to have
• • Simple, elegant design
• • Aesthetically compatible with our website design (www.valdanecompanies.com)
• • Color palette including but not limited to white, black, and red (as per logos)
Should not have
• - Not too much red color
• - Do not stack both logos on top of each other

```html
<!DOCTYPE html>
<html lang="en">
<head>
<meta charset="utf-8">
<title>Valdane Companies Business Card</title>
<link href="https://fonts.googleapis.com/css2?family=Tinos:wght@400;700&family=Lato:wght@400&display=swap" rel="stylesheet">
<style>
  :root {
    --crimson: #a31d34;
    --crimson-deep: #8e1729;
    --paper: #ffffff;
    --ink: #3a3f4d;
    --rule: #4a5064;
    --stage: #e9e9eb;
  }
  * { box-sizing: border-box; margin: 0; padding: 0; }
  html, body { width: 1200px; height: 800px; overflow: hidden; }
  body {
    background: var(--stage);
    font-family: "Tinos", "Times New Roman", serif;
    position: relative;
  }
  .card {
    position: absolute;
    left: 320px;
    width: 560px;
    height: 320px;
    border-radius: 12px;
    overflow: hidden;
    box-shadow: 0 6px 18px rgba(0,0,0,0.18);
  }

  /* Front */
  .card-front { top: 60px; background: var(--crimson); color: var(--paper); }
  .front-brand {
    position: absolute; left: 0; right: 0; top: 118px;
    display: flex; align-items: center; justify-content: center; gap: 16px;
  }
  .brand-square { width: 22px; height: 22px; background: currentColor; }
  .brand-name {
    font-weight: 700; font-size: 27px; letter-spacing: 2px; text-transform: uppercase;
  }
  .front-web {
    position: absolute; left: 0; right: 0; top: 210px; text-align: center;
    font-size: 12px; letter-spacing: 4px;
  }
  .front-web .domain { text-transform: uppercase; font-weight: 700; }

  /* Back */
  .card-back { top: 420px; background: var(--paper); }
  .back-band {
    position: absolute; left: 0; top: 0; bottom: 0; width: 92px;
    background: var(--crimson); border-right: 3px solid var(--rule);
  }
  .back-brand {
    position: absolute; left: 128px; top: 52px;
    display: flex; align-items: center; gap: 12px; color: var(--crimson);
  }
  .back-brand .brand-name { font-size: 24px; }
  .back-brand .brand-square { width: 18px; height: 18px; }
  .divider {
    position: absolute; left: 128px; right: 34px; top: 116px;
    height: 1.5px; background: var(--rule);
  }
  .person { position: absolute; left: 128px; top: 134px; }
  .person-name { color: var(--crimson); font-weight: 700; font-size: 21px; }
  .person-title { color: var(--ink); font-size: 14px; margin-top: 1px; }
  .contacts { position: absolute; left: 128px; top: 196px; list-style: none; }
  .contacts li {
    display: flex; align-items: center; gap: 10px;
    color: var(--ink); font-size: 14px; line-height: 24px;
  }
  .contacts svg { width: 13px; height: 13px; fill: var(--crimson); flex: none; }
  .contacts .web-accent { color: var(--crimson); }
  .address {
    position: absolute; right: 34px; bottom: 40px; text-align: right;
    color: var(--ink); font-size: 14px; line-height: 20px; font-style: normal;
  }
</style>
</head>
<body>

<section class="card card-front" aria-label="Card front">
  <div class="front-brand">
    <span class="brand-square"></span>
    <span class="brand-name">Thornmere Regional Center</span>
  </div>
  <p class="front-web">www.<span class="domain">Valdanecompanies</span>.com</p>
</section>

<section class="card card-back" aria-label="Card back">
  <div class="back-band"></div>
  <div class="back-brand">
    <span class="brand-square"></span>
    <span class="brand-name">Thornmere Regional Center</span>
  </div>
  <div class="divider"></div>
  <div class="person">
    <p class="person-name">Marcus Valdane</p>
    <p class="person-title">CEO</p>
  </div>
  <ul class="contacts">
    <li>
      <svg viewBox="0 0 16 16"><path d="M4 0h8a1.5 1.5 0 0 1 1.5 1.5v13A1.5 1.5 0 0 1 12 16H4a1.5 1.5 0 0 1-1.5-1.5v-13A1.5 1.5 0 0 1 4 0zm0.5 2v10.5h7V2z"/></svg>
      +1.555.314.2287
    </li>
    <li>
      <svg viewBox="0 0 16 16"><path d="M3.6 1l2.6 3-1.5 1.8a9 9 0 0 0 5.5 5.5L12 9.8l3 2.6-1.6 2.6C7.5 15.5.5 8.5 1 2.6z"/></svg>
      +1.555.628.4410
    </li>
    <li>
      <svg viewBox="0 0 16 16"><path d="M0 3h16v10H0zm1.5 1.3v.4L8 9l6.5-4.3v-.4z"/></svg>
      mvaldane@valdanecompanies.com
    </li>
    <li>
      <svg viewBox="0 0 16 16"><path d="M8 0a8 8 0 1 0 0 16A8 8 0 0 0 8 0zm0 1.5c1 0 2 1.9 2.3 5.5H5.7C6 3.4 7 1.5 8 1.5zM1.6 9h2.6c.1 2 .5 3.8 1.2 4.9A6.5 6.5 0 0 1 1.6 9zm4.1 0h4.6C10 12.6 9 14.5 8 14.5S6 12.6 5.7 9zm6.1 0h2.6a6.5 6.5 0 0 1-3.8 4.9c.7-1.1 1.1-2.9 1.2-4.9zM1.6 7a6.5 6.5 0 0 1 3.8-4.9C4.7 3.2 4.3 5 4.2 7zm10.2 0c-.1-2-.5-3.8-1.2-4.9A6.5 6.5 0 0 1 14.4 7z"/></svg>
      <span>www.<span class="web-accent">valdanecompanies</span>.com</span>
    </li>
  </ul>
  <address class="address">
    Larkfield Court 5<br>
    4817 Vista Orilla<br>
    Alder Vale, CA.
  </address>
</section>

</body>
</html>
```